Black Matte card with samurai logo which I would like it to be textured and company name on one side and on the other side I would like the company information with the reno (Face logo) Sushi logo. Double Sided card.

majority customers are University students, University sororities and fraternities.

It Company

Reno Sushi
317 W. Harlow Ave
Tucson, AZ 85042
Phone (520)413-6271
Fax (520)357-1846
E-mail: Renosushidesert@mailbox-example.com
FB: Renosushidesert
Twitter: Renosushidesert

• Present Normal

```html
<!DOCTYPE html>
<html lang="en">
<head>
<meta charset="utf-8">
<title>Reno Sushi – Business Card</title>
<link href="https://fonts.googleapis.com/css2?family=PT+Sans:wght@400&display=swap" rel="stylesheet">
<style>
  :root {
    --bg: #e9e4dc;
    --matte: #1b1b1b;
    --matte-light: #2a2a2a;
    --paper: #ffffff;
    --ink: #1e1e1e;
    --red: #c8343a;
    --red-dark: #a8262b;
    --white: #ffffff;
  }
  * { box-sizing: border-box; margin: 0; padding: 0; }
  html, body {
    width: 1200px; height: 1164px; overflow: hidden;
    background: var(--bg);
    font-family: "PT Sans", Arial, sans-serif;
  }
  .canvas { position: relative; width: 1200px; height: 1164px; }

  .card { position: absolute; border-radius: 38px; overflow: hidden; }

  /* Front side */
  .card-front {
    left: 26px; top: 18px; width: 910px; height: 517px;
    background: radial-gradient(ellipse at 45% 40%, var(--matte-light), var(--matte) 75%);
  }
  .front-emblem {
    position: absolute; left: 325px; top: 54px; width: 325px; height: 295px;
    border-radius: 10px;
    background: linear-gradient(160deg, #f2f2f2 0%, #d9d9d9 55%, #b73a3e 100%);
    opacity: .9;
  }
  .front-name {
    position: absolute; left: 0; width: 100%; top: 368px;
    text-align: center; color: var(--red);
    font-size: 74px; line-height: 1; letter-spacing: 1px;
  }

  /* Back side */
  .card-back {
    left: 240px; top: 581px; width: 908px; height: 517px;
    background: var(--paper);
  }
  .back-emblem {
    position: absolute; left: 361px; top: 26px; width: 180px; height: 169px;
    border-radius: 6px;
    background: linear-gradient(160deg, #2a2a2a 0%, #3a3a3a 60%, #c0393e 100%);
  }
  .back-name {
    position: absolute; left: 0; width: 100%; text-align: center; color: var(--red);
  }
  .back-name .primary { display: block; position: absolute; top: 210px; width: 100%; font-size: 60px; line-height: 1; }
  .back-name .secondary { display: block; position: absolute; top: 270px; width: 100%; font-size: 27px; line-height: 1; color: var(--ink); letter-spacing: 1px; }

  .band { position: absolute; left: 0; top: 0; width: 908px; height: 517px; }

  .contact {
    position: absolute; left: 0; width: 100%; color: var(--white);
    font-size: 21px; line-height: 1; text-align: center;
  }
  .contact-row {
    position: absolute; left: 0; width: 100%;
    display: flex; justify-content: center; align-items: center; gap: 10px;
  }
  .contact-row.phones { top: 372px; }
  .contact-row.email { top: 407px; }
  .contact-row.social { top: 442px; }
  .contact-row.address { top: 488px; font-size: 22px; }
  .contact-item { display: inline-flex; align-items: center; gap: 8px; }
  .contact-row .gap { width: 10px; }
  .icon { width: 18px; height: 18px; display: block; }
  .social-square { width: 18px; height: 18px; border-radius: 3px; background: #4a78b8; display: block; }
  .social-square.alt { background: #5aaee0; }
</style>
</head>
<body>
<div class="canvas">

  <section class="card card-front" aria-label="Card front">
    <div class="front-emblem" role="img" aria-label="Samurai mascot holding a sword and a red fish"></div>
    <div class="front-name">reno sushi</div>
  </section>

  <section class="card card-back" aria-label="Card back">
    <div class="back-emblem" role="img" aria-label="Samurai mascot holding a sword and a red fish"></div>
    <div class="back-name">
      <span class="primary">reno</span>
      <span class="secondary">sushi</span>
    </div>

    <svg class="band" viewBox="0 0 908 517" aria-hidden="true">
      <path d="M0 428 Q454 230 908 428" fill="none" stroke="var(--red)" stroke-width="4"/>
      <path d="M0 436 Q454 266 908 436 L908 517 L0 517 Z" fill="var(--ink)"/>
    </svg>

    <div class="contact">
      <div class="contact-row phones">
        <span class="contact-item">
          <svg class="icon" viewBox="0 0 18 18"><path d="M4 2 L7 2 L8 6 L6 7.5 Q7.5 10.5 10.5 12 L12 10 L16 11 L16 14 Q14 16.5 10 15 Q4 12.5 2.5 6 Q2 3.5 4 2 Z" fill="var(--white)"/></svg>
          (520)413-6271
        </span>
        <span class="gap"></span>
        <span class="contact-item">
          <svg class="icon" viewBox="0 0 18 18"><rect x="5" y="1" width="8" height="16" rx="1.5" fill="var(--white)"/><rect x="6.5" y="3" width="5" height="5" fill="var(--ink)"/></svg>
          (520)357-1846
        </span>
      </div>
      <div class="contact-row email">
        <span class="contact-item">
          <svg class="icon" viewBox="0 0 18 18"><rect x="1" y="4" width="16" height="11" rx="1" fill="var(--white)"/><path d="M1.5 4.5 L9 10 L16.5 4.5" fill="none" stroke="var(--ink)" stroke-width="1.4"/></svg>
          Renosushidesert@mailbox-example.com
        </span>
      </div>
      <div class="contact-row social">
        <span class="contact-item"><span class="social-square"></span>Renosushidesert</span>
        <span class="gap"></span>
        <span class="contact-item"><span class="social-square alt"></span>Renosushidesert</span>
      </div>
      <div class="contact-row address">Reno Sushi 317 W. Harlow Ave Tucson, AZ 85042</div>
    </div>
  </section>

</div>
</body>
</html>
```